Pup Snack Den - New Website Design

Create a professional Storvana website for a the hottest trend; a Pup Snack Den subscription box business. Storvana.com is an easy to use website builder.
Please see frellonbox.com; gummotrove.com and wagcrate.com for the concept I am after. The business has not been launched yet, I am currently in the pre-launch stage using a specialized landing page website, and so the time scale for developing my professional looking Storvana website is up to 1-2 weeks.
The webpage should have a fun feel and should match the style of the company logo at gummotrove.com. The pages to include are 'Home', 'About us' and 'Get Started'
Thank you and good luck!

```html
<!DOCTYPE html>
<html lang="en">
<head>
<meta charset="utf-8">
<title>Pup Snack Den</title>
<link href="https://fonts.googleapis.com/css2?family=Raleway:wght@500;600;700;800&family=Open+Sans:ital,wght@0,400;0,600;0,700;1,400&display=swap" rel="stylesheet">
<style>
:root{
  --green:#8cbd4f;
  --green-dark:#7aab3e;
  --blue:#3ea7df;
  --ink:#2b2b2b;
  --text:#6d6d6d;
  --muted:#9a9a9a;
  --line:#dcdcdc;
  --topbar:#2f2f2f;
  --footer:#262626;
  --footer-base:#1d1d1d;
  --price:#3ea7df;
}
*{margin:0;padding:0;box-sizing:border-box}
html,body{width:1200px;height:3782px;overflow:hidden}
body{position:relative;background:#fff;font-family:"Open Sans",Arial,sans-serif;color:var(--text)}
.abs{position:absolute}
h1,h2,h3,h4,.brand,.menu a{font-family:"Raleway",Arial,sans-serif}

/* top bar */
.topbar{left:0;top:0;width:1200px;height:30px;background:var(--topbar);color:#e6e6e6;font-size:11px;font-weight:600}
.topbar .left{left:98px;top:8px;display:flex;gap:22px}
.topbar .right{right:98px;top:8px;display:flex;gap:20px}
.topbar span{display:flex;align-items:center;gap:6px}
.topbar svg{width:11px;height:11px;fill:#e6e6e6}

/* header */
.header{left:0;top:30px;width:1200px;height:86px;background:#fff}
.brand{left:98px;top:30px;font-size:24px;font-weight:800;color:var(--ink);letter-spacing:.2px}
.menu{left:430px;top:36px;display:flex;gap:30px}
.menu a{font-size:15px;font-weight:700;color:var(--ink);text-decoration:none;letter-spacing:.3px}
.menu a.active{color:var(--green)}
.hbtn{top:26px;width:38px;height:38px;border-radius:50%;display:flex;align-items:center;justify-content:center}
.hbtn.search{left:1010px;border:2px solid var(--green)}
.hbtn.cart{left:1058px;background:var(--green)}

/* hero */
.hero{left:0;top:116px;width:1200px;height:494px;background:linear-gradient(180deg,#4d6b32 0%,#6f8a48 40%,#8b8f5a 70%,#6a5a40 100%)}
.hero-title{left:0;top:158px;width:1200px;text-align:center;font-size:56px;font-weight:800;color:#fff;letter-spacing:1px}
.hero-sub{left:0;top:226px;width:1200px;text-align:center;font-size:19px;font-weight:600;color:#fff}
.hero-arrow{top:350px;width:16px;height:24px}

/* welcome */
.welcome h2{left:98px;top:702px;font-size:27px;font-weight:700;color:var(--ink)}
.welcome p{left:98px;width:482px;font-size:12.5px;line-height:22px;color:var(--text)}
.btn-outline{border:2px solid var(--line);border-radius:22px;color:var(--green);font-family:"Raleway",Arial,sans-serif;font-weight:700;font-size:12px;text-align:center;letter-spacing:.5px}
.frame{left:693px;top:686px;width:406px;height:347px;background:var(--blue)}
.welcome-photo{left:650px;top:711px;width:421px;height:292px;background:linear-gradient(135deg,#b89866 0%,#7a5a3a 45%,#5f8d3d 75%,#4f7a33 100%);border:6px solid #fff}

.divider{left:98px;width:1001px;height:1px;background:var(--line)}
.section-title{left:0;width:1200px;text-align:center;font-size:27px;font-weight:700;color:var(--ink)}

/* products */
.card{top:1237px;width:240px;height:252px;border:1px solid var(--line);background:#f6f6f6}
.card .thumb{position:absolute;left:20px;top:62px;width:198px;height:128px;border-radius:4px}
.pname{top:1512px;width:240px;text-align:center;font-family:"Raleway",Arial,sans-serif;font-size:19px;font-weight:700;color:var(--ink)}
.price{top:1547px;width:240px;text-align:center;font-size:15px}
.price s{color:var(--muted);margin-right:6px}
.price b{color:var(--price);font-weight:600}
.add{top:1584px;width:120px;height:36px;line-height:32px;font-size:11px}
.btn-green{left:484px;top:1681px;width:232px;height:43px;line-height:43px;background:var(--green);color:#fff;border-radius:22px;text-align:center;font-family:"Raleway",Arial,sans-serif;font-weight:700;font-size:12.5px;letter-spacing:.5px}

/* testimonial */
.testimonial{left:0;top:1809px;width:1200px;height:449px;background:linear-gradient(90deg,#7d6a4a 0%,#8a7650 22%,#5d7a33 45%,#6e8c3c 70%,#587530 100%)}
.quote-text{left:580px;top:1955px;width:530px;font-size:12.5px;line-height:24px;font-style:italic;color:#fff}
.quote-rule{left:580px;top:2060px;width:145px;height:1px;background:rgba(255,255,255,.6)}
.avatar{left:584px;top:2076px;width:86px;height:86px;border-radius:50%;border:4px solid #fff;background:linear-gradient(135deg,#c89c7e,#6b4f3d)}
.author{left:590px;top:2176px;font-family:"Raleway",Arial,sans-serif;font-weight:700;font-size:15px;color:#fff}
.dots{left:1050px;top:2189px;display:flex;gap:5px}
.dots i{width:12px;height:12px;border-radius:50%;border:2px solid #fff;display:block}
.dots i.on{background:#fff}

/* offer */
.offer{left:98px;top:2374px;width:527px;height:297px;background:var(--blue);color:#fff}
.offer h3{position:absolute;left:42px;top:58px;font-size:27px;font-weight:700}
.offer p{position:absolute;left:42px;top:110px;width:450px;font-size:12px;line-height:20px}
.offer .range{position:absolute;left:42px;top:208px;font-size:16px;font-weight:600}
.offer .range b{font-size:24px;font-weight:700}
.video{left:625px;top:2344px;width:476px;height:357px;background:linear-gradient(160deg,#e9e3d8 0%,#d2c5b1 45%,#8b6f52 75%,#5a4532 100%);border:4px solid #fff;box-shadow:0 2px 8px rgba(0,0,0,.15)}
.play{left:766px;top:2490px;width:60px;height:60px;border-radius:50%;background:#1e1e1e}

/* blog */
.blog-img{top:2933px;width:207px;height:182px}
.blog-title{top:2935px;font-family:"Raleway",Arial,sans-serif;font-weight:700;font-size:17px;color:var(--ink)}
.blog-meta{top:2970px;font-size:11px;color:var(--muted);display:flex;gap:16px}
.blog-meta span{display:flex;align-items:center;gap:5px}
.blog-text{top:2998px;width:240px;font-size:11.5px;line-height:21px;color:var(--text)}
.blog-more{top:3088px;font-family:"Raleway",Arial,sans-serif;font-weight:700;font-size:11.5px;color:var(--green)}

/* help band */
.help{left:0;top:3193px;width:1200px;height:209px;background:var(--green);color:#fff}
.help h2{position:absolute;left:0;top:38px;width:1200px;text-align:center;font-size:25px;font-weight:700}
.feature{top:3295px;display:flex;gap:16px;align-items:center;color:#fff}
.feature svg{width:58px;height:58px;fill:#fff}
.feature h4{font-size:18px;font-weight:700}
.feature p{font-size:11.5px;margin-top:2px}

/* footer */
.footer{left:0;top:3402px;width:1200px;height:313px;background:var(--footer)}
.fcol h4{font-family:"Raleway",Arial,sans-serif;font-size:17px;font-weight:700;color:#fff;margin-bottom:14px}
.fcol ul{list-style:none}
.fcol li{font-size:11.5px;color:#d0d0d0;line-height:29px}
.fcontact{display:flex;gap:16px;align-items:flex-start;font-size:11.5px;color:#d0d0d0;line-height:20px}
.fcontact svg{width:14px;height:16px;fill:#fff;flex:none;margin-top:2px}
.base{left:0;top:3715px;width:1200px;height:67px;background:var(--footer-base);border-top:1px solid #3a3a3a;text-align:center;line-height:50px;font-size:11.5px;color:#d0d0d0}
</style>
</head>
<body>

<!-- top bar -->
<div class="abs topbar">
  <div class="abs left">
    <span><svg viewBox="0 0 16 16"><path d="M3 1l3 3-2 2c1 2 3 4 5 5l2-2 3 3-2 3C6 14 2 10 0 3z"/></svg>1 800 555 0142</span>
    <span><svg viewBox="0 0 16 16"><path d="M0 3h16v10H0zM1 4l7 5 7-5"/></svg>sales@pupsnackden.com</span>
  </div>
  <div class="abs right">
    <span><svg viewBox="0 0 16 16"><path d="M4 13l-3-4 2-2 2 2 7-7 2 2z"/></svg>Checkout</span>
    <span><svg viewBox="0 0 16 16"><path d="M8 15L1 8a4 4 0 017-5 4 4 0 017 5z"/></svg>Wishlist</span>
    <span><svg viewBox="0 0 16 16"><circle cx="8" cy="5" r="4"/><path d="M0 16c0-5 16-5 16 0z"/></svg>My Account</span>
    <span><svg viewBox="0 0 16 16"><rect x="2" y="7" width="12" height="9"/><path d="M4 7V5a4 4 0 018 0v2h-2V5a2 2 0 00-4 0v2z"/></svg>Login</span>
    <span><svg viewBox="0 0 16 16"><path d="M11 1l4 4-9 9H2v-4z"/></svg>Register</span>
  </div>
</div>

<!-- header -->
<header class="abs header">
  <div class="abs brand">PUP SNACK DEN</div>
  <nav class="abs menu">
    <a class="active">HOME</a><a>ABOUT</a><a>ACCESSORIES</a><a>NEW ARRIVALS</a><a>FOOD</a><a>SALE</a>
  </nav>
  <div class="abs hbtn search"><svg width="16" height="16" viewBox="0 0 16 16"><circle cx="6.5" cy="6.5" r="5" fill="none" stroke="#8cbd4f" stroke-width="2"/><path d="M10 10l5 5" stroke="#8cbd4f" stroke-width="2"/></svg></div>
  <div class="abs hbtn cart"><svg width="18" height="18" viewBox="0 0 18 18"><path d="M1 2h3l2 9h9l2-7H5" fill="none" stroke="#fff" stroke-width="2"/><circle cx="7" cy="15" r="1.6" fill="#fff"/><circle cx="14" cy="15" r="1.6" fill="#fff"/></svg></div>
</header>

<!-- hero -->
<section class="abs hero" role="img" aria-label="Three puppies sitting side by side on a wooden bench in a garden"></section>
<div class="abs hero-title">PUP SNACK DEN</div>
<div class="abs hero-sub">Nemo enim ipsam voluptatem quia voluptas sit aspernatur aut odit au</div>
<svg class="abs hero-arrow" style="left:8px" viewBox="0 0 16 24"><path d="M12 3L4 12l8 9" fill="none" stroke="#fff" stroke-width="3"/></svg>
<svg class="abs hero-arrow" style="left:1176px" viewBox="0 0 16 24"><path d="M4 3l8 9-8 9" fill="none" stroke="#fff" stroke-width="3"/></svg>

<!-- welcome -->
<section class="welcome">
  <h2 class="abs">WELCOME TO PUP SNACK DEN</h2>
  <p class="abs" style="top:754px">Nam libero tempore, cum soluta nobis est eligendi optio cumque nihil impedit quo minus id quod maxime placeat facere.</p>
  <p class="abs" style="top:830px">Possimus, omnis voluptas assumenda est, omnis dolor repellendus. Temporibus autem quibusdam et aut officiis debitis aut rerum necessitatibus saepe eveniet ut et voluptates repudiandae sint mo lestiae non recusandae. Itaque earum rer um hic tenetur a sapiente delectus, ut aut.</p>
  <div class="abs btn-outline" style="left:98px;top:948px;width:129px;height:40px;line-height:36px">READ MORE</div>
  <div class="abs frame"></div>
  <div class="abs welcome-photo" role="img" aria-label="Several dogs eating from metal bowls on a lawn"></div>
</section>

<div class="abs divider" style="top:1106px"></div>

<!-- featured products -->
<h2 class="abs section-title" style="top:1164px">FEATURED PRODUCTS</h2>

<div class="abs card" style="left:98px"><div class="thumb" role="img" aria-label="Bone shaped dog biscuits" style="background:linear-gradient(135deg,#d9a15a,#a8692f)"></div></div>
<div class="abs card" style="left:353px"><div class="thumb" role="img" aria-label="Puppy beside a blue food bowl" style="background:linear-gradient(135deg,#f3efe6 0%,#e8e0cf 55%,#3b8fd6 100%)"></div></div>
<div class="abs card" style="left:607px"><div class="thumb" role="img" aria-label="Red dog collar" style="background:linear-gradient(135deg,#f5f5f5 0%,#d8313e 60%,#b7212c 100%)"></div></div>
<div class="abs card" style="left:861px"><div class="thumb" role="img" aria-label="Dog resting on a round pet bed" style="background:linear-gradient(135deg,#efe4d2,#b99670)"></div></div>

<div class="abs pname" style="left:98px">Tempo autem quib</div>
<div class="abs pname" style="left:353px">Tempo autem quib</div>
<div class="abs pname" style="left:607px">Tempo autem quib</div>
<div class="abs pname" style="left:861px">Tempo autem quib</div>

<div class="abs price" style="left:98px"><s>$45.00</s><b>$30.00</b></div>
<div class="abs price" style="left:353px"><s>$45.00</s><b>$30.00</b></div>
<div class="abs price" style="left:607px"><s>$45.00</s><b>$30.00</b></div>
<div class="abs price" style="left:861px"><s>$45.00</s><b>$30.00</b></div>

<div class="abs btn-outline add" style="left:158px">ADD TO CART</div>
<div class="abs btn-outline add" style="left:413px">ADD TO CART</div>
<div class="abs btn-outline add" style="left:667px">ADD TO CART</div>
<div class="abs btn-outline add" style="left:921px">ADD TO CART</div>

<div class="abs btn-green">VIEW MORE PRODUCTS</div>

<!-- testimonial -->
<section class="abs testimonial" role="img" aria-label="Beagle puppy lying in tall green grass"></section>
<svg class="abs" style="left:580px;top:1880px" width="62" height="50" viewBox="0 0 62 50"><path d="M0 50V26C0 10 8 2 24 0v10c-8 2-11 7-11 14h11v26zM36 50V26C36 10 44 2 60 0v10c-8 2-11 7-11 14h11v26z" fill="#fff"/></svg>
<p class="abs quote-text">At vero eos et accusamus et iusto odio dignissimos ducimus qui blanditiis praesentium voluptatum deleniti atque corrupti quos dolores et quas molestias excepturi sintoae occaecati cupiditate non provident, similique sunt.</p>
<div class="abs quote-rule"></div>
<div class="abs avatar" role="img" aria-label="Customer portrait"></div>
<div class="abs author">John Doe</div>
<div class="abs dots"><i class="on"></i><i></i><i></i></div>

<!-- offer -->
<section class="abs offer">
  <h3>Save Up To 30% Off In This Week</h3>
  <p>Nam libero tempore, cum soluta nobis est eligendi optio cumque nihilimp edit quo minus id quod maxime placeat facere possimus, omnis voluptas assumenda est, omnis dolor repellendus.</p>
  <div class="range">From <b>$30.99</b> To <b>$60.99</b></div>
</section>
<div class="abs video" role="img" aria-label="Little girl feeding a brown puppy on a kitchen floor"></div>
<div class="abs play"><svg width="60" height="60" viewBox="0 0 60 60"><path d="M24 18l18 12-18 12z" fill="#fff"/></svg></div>

<div class="abs divider" style="top:2787px"></div>

<!-- blog -->
<h2 class="abs section-title" style="top:2852px">LATEST BLOG</h2>

<div class="abs blog-img" style="left:98px;background:linear-gradient(135deg,#c49470,#7a4a2e 60%,#dcd6cf)" role="img" aria-label="Woman laughing while hugging her dog"></div>
<div class="abs blog-title" style="left:325px">Finibus Bonorum et Malorum</div>
<div class="abs blog-meta" style="left:325px"><span><svg width="11" height="11" viewBox="0 0 12 12"><rect x="1" y="2" width="10" height="9" fill="none" stroke="#8cbd4f" stroke-width="1.5"/><path d="M1 5h10" stroke="#8cbd4f"/></svg>07/07/2017</span><span><svg width="11" height="11" viewBox="0 0 12 12"><circle cx="6" cy="4" r="3" fill="#8cbd4f"/><path d="M0 12c0-4 12-4 12 0z" fill="#8cbd4f"/></svg>John Doe</span></div>
<p class="abs blog-text" style="left:325px">Nam libero tempore, cum soluta nobis est e ligendi optio cumque nihil impedit quo min us id quod maxime plac</p>
<div class="abs blog-more" style="left:325px">READ MORE &gt;&gt;</div>

<div class="abs blog-img" style="left:627px;background:linear-gradient(135deg,#9b9890,#5e5a52 55%,#b58a5c)" role="img" aria-label="Person walking two dogs on leashes"></div>
<div class="abs blog-title" style="left:854px">Finibus Bonorum et Malorum</div>
<div class="abs blog-meta" style="left:854px"><span><svg width="11" height="11" viewBox="0 0 12 12"><rect x="1" y="2" width="10" height="9" fill="none" stroke="#8cbd4f" stroke-width="1.5"/><path d="M1 5h10" stroke="#8cbd4f"/></svg>07/07/2017</span><span><svg width="11" height="11" viewBox="0 0 12 12"><circle cx="6" cy="4" r="3" fill="#8cbd4f"/><path d="M0 12c0-4 12-4 12 0z" fill="#8cbd4f"/></svg>John Doe</span></div>
<p class="abs blog-text" style="left:854px">Nam libero tempore, cum soluta nobis est e ligendi optio cumque nihil impedit quo min us id quod maxime plac</p>
<div class="abs blog-more" style="left:854px">READ MORE &gt;&gt;</div>

<!-- help -->
<section class="abs help"><h2>HOW CAN WE HELP YOU?</h2></section>
<svg class="abs" style="left:50px;top:3312px" width="14" height="24" viewBox="0 0 14 24"><path d="M11 3L3 12l8 9" fill="none" stroke="rgba(255,255,255,.7)" stroke-width="3"/></svg>
<svg class="abs" style="left:1136px;top:3312px" width="14" height="24" viewBox="0 0 14 24"><path d="M3 3l8 9-8 9" fill="none" stroke="rgba(255,255,255,.7)" stroke-width="3"/></svg>

<div class="abs feature" style="left:98px"><svg viewBox="0 0 48 48"><path d="M8 4h32a4 4 0 014 4v30a3 3 0 01-3 3h-1v4h-6v-4H14v4H8v-4H7a3 3 0 01-3-3V8a4 4 0 014-4zm2 6v14h28V10zm2 22a3 3 0 100 6 3 3 0 000-6zm24 0a3 3 0 100 6 3 3 0 000-6z"/></svg><div><h4>Free Shipping</h4><p>Ducimus qui blanditiis</p></div></div>
<div class="abs feature" style="left:355px"><svg viewBox="0 0 48 48"><path d="M10 22h28v24H10zM15 22v-6a9 9 0 0118 0v6h-5v-6a4 4 0 00-8 0v6z"/></svg><div><h4>100% Secure</h4><p>Ducimus qui blanditiis</p></div></div>
<div class="abs feature" style="left:603px"><svg viewBox="0 0 48 48"><path d="M8 10h32v22H8zm3 3v16h26V13zM2 35h44v3H2z"/></svg><div><h4>Best Online</h4><p>Ducimus qui blanditiis</p></div></div>
<div class="abs feature" style="left:855px"><svg viewBox="0 0 48 48"><circle cx="24" cy="14" r="7"/><path d="M11 40c0-14 26-14 26 0z"/><circle cx="10" cy="18" r="5"/><path d="M0 38c0-10 14-11 17-6-3 2-4 4-4 6z"/><circle cx="38" cy="18" r="5"/><path d="M48 38c0-10-14-11-17-6 3 2 4 4 4 6z"/></svg><div><h4>Customer Support</h4><p>Ducimus qui blanditiis</p></div></div>

<!-- footer -->
<footer class="abs footer"></footer>
<div class="abs fcol" style="left:98px;top:3478px">
  <h4>Contact Us</h4>
  <div class="fcontact" style="margin-top:22px"><svg viewBox="0 0 14 18"><path d="M7 0a6 6 0 016 6c0 5-6 12-6 12S1 11 1 6a6 6 0 016-6zm0 3a3 3 0 100 6 3 3 0 000-6z"/></svg><div>48 Larkfield Lane,<br>Lyon France</div></div>
  <div class="fcontact" style="margin-top:18px"><svg viewBox="0 0 16 16"><path d="M3 1l3 3-2 2c1 2 3 4 5 5l2-2 3 3-2 3C6 14 2 10 0 3z"/></svg><div>1 800 555 0142</div></div>
  <div class="fcontact" style="margin-top:20px"><svg viewBox="0 0 16 16"><path d="M0 3h16v10H0z"/></svg><div>sales@pupsnackden.com</div></div>
</div>
<div class="abs fcol" style="left:355px;top:3478px"><h4>Information</h4><ul><li>About Us</li><li>Careers</li><li>Privacy &amp; Security</li><li>Site Map</li><li>Terms of Use</li><li>Blog</li></ul></div>
<div class="abs fcol" style="left:524px;top:3478px"><h4>Help &amp; support</h4><ul><li>Recommended Reading</li><li>Submit your Story</li><li>Contact Us</li><li>Frequently Asked Questions</li><li>How to Order</li></ul></div>
<div class="abs fcol" style="left:753px;top:3478px"><h4>My Account</h4><ul><li>Delivery Information</li><li>My Account</li><li>Order Tracking</li><li>Reminder Service</li><li>Shipping, Returns &amp; Fees</li></ul></div>
<div class="abs fcol" style="left:970px;top:3478px"><h4>Shop with us</h4><ul><li>Shop by Brand</li><li>PawPoints</li><li>Gift Cards &amp; eCertificates</li><li>Return Policy</li><li>Track Your Order</li></ul></div>

<div class="abs base">Copyrights © 2017, Pup Snack Den. All Rights Reserved &nbsp;|&nbsp; Privacy Policy &nbsp;|&nbsp; Terms of Use &nbsp;|&nbsp; Feedback</div>

</body>
</html>
```